Low Testosterone Center Postcard Design

I need a jumbo direct mail marketing postcard for my men's low testosterone center. We evaluate and treat men with symptoms related to low testosterone. See my website www.oakridgewellclinic.com for more info on the symptoms of low testosterone and the benefits from bio identical replacement therapy. We have physician oversight for our program. Images and documents are available on my website.

Industry/Entity Type

Marketing

```html
<!DOCTYPE html>
<html lang="en">
<head>
<meta charset="utf-8">
<title>Oakridge Wellness Clinic – TRT Postcard</title>
<link href="https://fonts.googleapis.com/css2?family=Jost:wght@300;400;500;600;700&family=Barlow+Semi+Condensed:wght@600&display=swap" rel="stylesheet">
<style>
  :root{
    --backdrop:#636365;
    --card:#ffffff;
    --brand-blue:#0a6fba;
    --accent-gold:#f2a62b;
    --panel-grey:#e2e5ec;
    --ink:#222226;
    --body-ink:#3a3a40;
    --tick-red:#c8202e;
    --stamp-line:#6d6d70;
    --photo-warm-a:#e9dcd3;
    --photo-warm-b:#c9a896;
  }
  *{margin:0;padding:0;box-sizing:border-box}
  html,body{width:1200px;height:809px;overflow:hidden}
  body{background:var(--backdrop);font-family:"Jost",sans-serif;color:var(--ink);position:relative}
  .postcard{position:absolute;left:50px;top:50px;width:1100px;height:707px;background:var(--card)}
  .photo{position:absolute;top:32px;height:165px;background:linear-gradient(135deg,var(--photo-warm-a),var(--photo-warm-b))}
  .photo--1{left:16px;width:231px;background:linear-gradient(135deg,#f4f2f0,#d9cfc8)}
  .photo--2{left:263px;width:230px}
  .photo--3{left:510px;width:231px;background:linear-gradient(135deg,#f3ece6,#cfae9a)}
  .headline-band{position:absolute;left:16px;top:210px;width:725px;height:102px;background:var(--brand-blue);padding:20px 0 0 37px}
  .headline-band__lead{color:#fff;font-size:27px;font-weight:500;line-height:33px}
  .headline-band__accent{color:var(--accent-gold);font-size:27px;font-weight:500;line-height:33px;text-transform:uppercase;letter-spacing:.3px}
  .benefits{position:absolute;left:16px;top:328px;width:725px;height:311px;background:var(--panel-grey);padding:15px 0 0 38px}
  .benefits__title{font-size:26px;font-weight:600;line-height:32px}
  .benefits__subtitle{font-size:13px;font-weight:300;color:var(--body-ink);line-height:16px}
  .benefits__intro{margin-top:19px;font-size:13px;font-weight:300;color:var(--body-ink);line-height:19px;width:620px}
  .benefit-list{position:absolute;top:136px;list-style:none}
  .benefit-list--left{left:38px}
  .benefit-list--right{left:372px}
  .benefit-list li{font-size:14px;font-weight:500;line-height:19.8px;padding-left:20px;position:relative}
  .benefit-list li::before{content:"";position:absolute;left:1px;top:6px;width:11px;height:7px;border-left:1.6px solid var(--tick-red);border-bottom:1.6px solid var(--tick-red);transform:rotate(-50deg);transform-origin:left top;top:10px;width:10px;height:5px}
  .contact-row{position:absolute;left:36px;top:275px;display:flex;gap:20px;font-family:"Barlow Semi Condensed",sans-serif;font-weight:600;font-size:16.5px;color:var(--brand-blue)}
  .contact-row span{display:flex;align-items:center}
  .contact-row span::before{content:"";width:9px;height:9px;border-radius:50%;background:var(--brand-blue);margin-right:13px}
  .brand{position:absolute;left:760px;top:40px;width:120px;text-align:center}
  .brand__dot{width:66px;height:66px;border-radius:50%;background:var(--accent-gold);margin:0 auto 6px}
  .brand__name{font-size:12.5px;font-weight:600;line-height:15px;color:var(--ink);text-transform:uppercase}
  .stamp-box{position:absolute;left:977px;top:41px;width:97px;height:118px;border:1px solid var(--stamp-line)}
</style>
</head>
<body>
  <section class="postcard">
    <div class="photo photo--1" role="img" aria-label="Couple lying apart in bed looking unhappy"></div>
    <div class="photo photo--2" role="img" aria-label="Couple playfully sharing a strawberry"></div>
    <div class="photo photo--3" role="img" aria-label="Affectionate couple embracing in bed"></div>

    <div class="headline-band">
      <p class="headline-band__lead">We can make the difference</p>
      <p class="headline-band__accent">In how you feel about yourself</p>
    </div>

    <div class="benefits">
      <h2 class="benefits__title">Benefits of TRT</h2>
      <p class="benefits__subtitle">What are the Benefits of TRT (Testosterone Replacement Therapy)?</p>
      <p class="benefits__intro">Benefits of TRT (Testosterone Replacement Therapy) at The Oakridge Wellness Clinic vary based upon the pre-therapy low testosterone symptoms and other factors, but can include:</p>
      <ul class="benefit-list benefit-list--left">
        <li>Improved muscle mass and strength</li>
        <li>Increased energy and vitality</li>
        <li>Increased bone mineral density</li>
        <li>Improved sexual desire and performance</li>
        <li>Boosted energy</li>
        <li>Decreased irritability and depression</li>
      </ul>
      <ul class="benefit-list benefit-list--right">
        <li>Improved concentration and focus</li>
        <li>Improved motivation</li>
        <li>Decreased body fat</li>
        <li>Better mood</li>
        <li>Improved erectile function.</li>
      </ul>
      <div class="contact-row">
        <span>555-014-2280</span>
        <span>WWW.OAKRIDGEWELLCLINIC.COM</span>
        <span>240 Linden St. Suite B&nbsp; Fairview,&nbsp; NJ</span>
      </div>
    </div>

    <div class="brand">
      <div class="brand__dot"></div>
      <p class="brand__name">Oakridge Wellness Clinic</p>
    </div>

    <div class="stamp-box"></div>
  </section>
</body>
</html>
```